Local Roofing/Construction company business needs new biz card design

We need a new business card design, current cards are from the start of this operation and generic at best. We are a local Construction Company (General Contractor) with a majority of our work originating from insurance claims-exterior finish work is the main focus (Roofs-Siding-Gutters etc). Heavily involved with homeowners and the low ball offers they receive from insurance company's after a insurable event takes place. I have attached some of our original logo file(s) below.

```html
<!DOCTYPE html>
<html lang="en">
<head>
<meta charset="utf-8">
<title>Ridgeline Build Co. — Business Card</title>
<link rel="stylesheet" href="https://fonts.googleapis.com/css2?family=Open+Sans:wght@400;600;700&display=swap">
<style>
  :root {
    --backdrop: #222222;
    --paper: #f4f4f4;
    --brand-green: #4bb465;
    --pattern-green: #3fb866;
    --ink-dark: #10292a;
    --ink-body: #1b1b1b;
    --white: #ffffff;
  }
  * { box-sizing: border-box; margin: 0; padding: 0; }
  html, body {
    width: 1200px; height: 780px; overflow: hidden;
    background: var(--backdrop);
    font-family: "Open Sans", Arial, sans-serif;
  }
  .canvas {
    position: relative; width: 1200px; height: 780px;
    display: flex; align-items: center; justify-content: center; gap: 40px;
  }
  .card {
    position: relative; width: 540px; height: 309px;
    overflow: hidden; border-radius: 2px;
    box-shadow: 0 10px 30px rgba(0,0,0,.45);
  }
  /* Front */
  .card-front { background: var(--paper); color: var(--ink-body); }
  .brand {
    position: absolute; left: 24px; top: 24px;
    display: flex; align-items: center; gap: 10px;
  }
  .brand-square { width: 26px; height: 26px; background: var(--brand-green); }
  .brand-name {
    font-weight: 700; font-size: 21px; letter-spacing: .5px;
    color: var(--ink-dark); text-transform: uppercase;
  }
  .address {
    position: absolute; left: 24px; top: 82px;
    font-size: 13px; line-height: 18px;
  }
  .contacts {
    position: absolute; left: 24px; top: 150px;
    list-style: none; font-size: 13px; line-height: 20px;
  }
  .contacts li { display: flex; align-items: center; gap: 8px; }
  .contacts svg { width: 12px; height: 12px; flex: none; fill: var(--brand-green); }
  .person {
    position: absolute; right: 52px; top: 150px; text-align: right;
  }
  .person-name { font-size: 28px; font-weight: 700; line-height: 1.1; color: var(--ink-dark); }
  .person-name .first { color: var(--brand-green); }
  .person-title { font-size: 15px; font-weight: 400; margin-top: 2px; color: var(--ink-dark); }
  .edge-strip {
    position: absolute; right: 0; top: 168px; bottom: 0; width: 30px;
    background: var(--brand-green);
  }
  /* Back */
  .card-back { background: var(--pattern-green); }
  .back-pattern { position: absolute; inset: 0; background: var(--pattern-green); }
  .back-brand {
    position: absolute; right: 22px; bottom: 20px;
    display: flex; align-items: center; gap: 6px;
    font-weight: 700; font-size: 11px; color: var(--white); text-transform: uppercase;
  }
  .back-brand .brand-square { width: 14px; height: 14px; background: var(--white); }
</style>
</head>
<body>
<main class="canvas">
  <section class="card card-front" aria-label="Business card front">
    <div class="brand">
      <span class="brand-square"></span>
      <span class="brand-name">Ridgeline Build Co.</span>
    </div>
    <p class="address">482 Oak Hollow Ln<br>Fairbrook, MO 63019</p>
    <ul class="contacts">
      <li><svg viewBox="0 0 24 24"><path d="M6.6 10.8a15 15 0 0 0 6.6 6.6l2.2-2.2a1 1 0 0 1 1-.25 11.4 11.4 0 0 0 3.6.57 1 1 0 0 1 1 1V20a1 1 0 0 1-1 1A17 17 0 0 1 3 4a1 1 0 0 1 1-1h3.5a1 1 0 0 1 1 1 11.4 11.4 0 0 0 .57 3.6 1 1 0 0 1-.25 1z"/></svg>555-210-4836</li>
      <li><svg viewBox="0 0 24 24"><path d="M6.6 10.8a15 15 0 0 0 6.6 6.6l2.2-2.2a1 1 0 0 1 1-.25 11.4 11.4 0 0 0 3.6.57 1 1 0 0 1 1 1V20a1 1 0 0 1-1 1A17 17 0 0 1 3 4a1 1 0 0 1 1-1h3.5a1 1 0 0 1 1 1 11.4 11.4 0 0 0 .57 3.6 1 1 0 0 1-.25 1z"/></svg>555-210-7719 (Emergency)</li>
      <li><svg viewBox="0 0 24 24"><path d="M12 2a10 10 0 1 0 0 20 10 10 0 0 0 0-20zm6.9 6h-3a15 15 0 0 0-1.3-3.9A8 8 0 0 1 18.9 8zM12 4c.8 1.2 1.5 2.5 1.9 4h-3.8c.4-1.5 1.1-2.8 1.9-4zM4.3 14a8 8 0 0 1 0-4h3.4a16 16 0 0 0 0 4zm.8 2h3a15 15 0 0 0 1.3 3.9A8 8 0 0 1 5.1 16zm3-8h-3a8 8 0 0 1 4.3-3.9A15 15 0 0 0 8.1 8zM12 20c-.8-1.2-1.5-2.5-1.9-4h3.8c-.4 1.5-1.1 2.8-1.9 4zm2.3-6H9.7a14 14 0 0 1 0-4h4.6a14 14 0 0 1 0 4zm.3 5.9a15 15 0 0 0 1.3-3.9h3a8 8 0 0 1-4.3 3.9zM16.3 14a16 16 0 0 0 0-4h3.4a8 8 0 0 1 0 4z"/></svg>www.ridgelinebuildco.com</li>
      <li><svg viewBox="0 0 24 24"><path d="M3 5h18a1 1 0 0 1 1 1v12a1 1 0 0 1-1 1H3a1 1 0 0 1-1-1V6a1 1 0 0 1 1-1zm9 7.5L4 7.3V17h16V7.3z"/></svg>hello@ridgelinebuildco.com</li>
    </ul>
    <div class="person">
      <h1 class="person-name"><span class="first">Marta</span> Delvane</h1>
      <p class="person-title">Managing Director</p>
    </div>
    <div class="edge-strip"></div>
  </section>

  <section class="card card-back" aria-label="Business card back">
    <div class="back-pattern" role="img" aria-label="Repeating brand pattern in tonal green"></div>
    <div class="back-brand">
      <span class="brand-square"></span>
      <span>Ridgeline Build Co.</span>
    </div>
  </section>
</main>
</body>
</html>
```